Mandala Postcard Design

I am in need of a postcard to hand out at a Psychic Fair. I envision the card to having half-of-a Mandala (from my Facebook folder), touched up a bit to make it vibrant and bold. Others vendors will have cards w/photographic backgrounds doing yoga. I'd like mine to stand out for it's line-drawn "cartoonish" nature, solid-color nature. The wording would be my basic contact info and a short description ... something like: "Experience the Magic of Mandala Making ... Next Class will be held: (open space for writing, no lines) The art is contained in this Facebook folder. Lots to choose from, with my favorites being the stronger outlined designs.

https://www.examplesocial.net/Brightorbs/media_set?set=a.20462926615637197.2184852941.783542196&type=3
Updates

I just uploaded a few new drawings that might work better, since they are more round. I want to minimize the white space, for instance, avoid having the left & right corners empty. Another idea could be to use 1/4 mandalas in the corners. I'm ready to make a decision. I want it to look great, but as I gain drawing experience, I'll need to update my cards. Thanks! I'm not sure if this the place for this comment, but I'll also be needing a DVD label for my tutorials, and a front page design for a mandala coloring book.

Target Market(s)

Primarily women interested in metaphysical, psychic, meditation, reiki and a basic interest in art.

Font styles to use
Serif
Sans Serif

Requirements
Should not have
• Should not be on a dark card, really should be a plain white background, it seems, in order to stand out.

```html
<!DOCTYPE html>
<html lang="en">
<head>
<meta charset="utf-8">
<title>Experience the Magic of Mandala Making</title>
<link rel="stylesheet" href="https://fonts.googleapis.com/css2?family=Dawning+of+a+New+Day&family=Arimo&display=swap">
<style>
  :root {
    --paper: #ffffff;
    --ink: #222222;
    --yellow: #ffe94a;
    --pink: #f27bb3;
    --cyan: #3fb8e6;
    --red: #e42a2f;
    --purple: #8a5cc4;
    --green: #8cc63f;
    --peach: #f7c9a6;
  }
  html, body {
    margin: 0;
    padding: 0;
    overflow: hidden;
    background: var(--paper);
  }
  .postcard {
    position: relative;
    width: 1200px;
    height: 929px;
    background: var(--paper);
    overflow: hidden;
  }
  .artwork {
    position: absolute;
    inset: 0;
    width: 1200px;
    height: 929px;
  }
  .headline {
    position: absolute;
    left: 560px;
    top: 290px;
    width: 640px;
    margin: 0;
    text-align: center;
    font-family: "Dawning of a New Day", cursive;
    font-weight: 400;
    font-size: 62px;
    line-height: 66px;
    color: var(--ink);
    letter-spacing: 1px;
  }
  .class-date {
    position: absolute;
    left: 718px;
    top: 478px;
    margin: 0;
    font-family: "Arimo", sans-serif;
    font-size: 19px;
    color: var(--ink);
  }
</style>
</head>
<body>
<main class="postcard">
  <svg class="artwork" viewBox="0 0 1200 929" xmlns="http://www.w3.org/2000/svg">
    <defs>
      <radialGradient id="mandala-large-tones" cx="0.5" cy="0.5" r="0.5">
        <stop offset="0" stop-color="var(--yellow)"/>
        <stop offset="0.3" stop-color="var(--cyan)"/>
        <stop offset="0.55" stop-color="var(--pink)"/>
        <stop offset="0.8" stop-color="var(--yellow)"/>
        <stop offset="1" stop-color="var(--peach)"/>
      </radialGradient>
      <radialGradient id="mandala-corner-tones" cx="0.5" cy="0.5" r="0.5">
        <stop offset="0" stop-color="var(--yellow)"/>
        <stop offset="0.4" stop-color="var(--cyan)"/>
        <stop offset="0.75" stop-color="var(--pink)"/>
        <stop offset="1" stop-color="var(--cyan)"/>
      </radialGradient>
      <radialGradient id="mandala-flower-tones" cx="0.5" cy="0.5" r="0.5">
        <stop offset="0" stop-color="var(--pink)"/>
        <stop offset="0.35" stop-color="var(--yellow)"/>
        <stop offset="0.7" stop-color="var(--cyan)"/>
        <stop offset="1" stop-color="var(--pink)"/>
      </radialGradient>
    </defs>
    <circle class="mandala mandala--half-left" cx="95" cy="455" r="420"
            fill="url(#mandala-large-tones)"
            role="img" aria-label="Half of a bold, colourful line-drawn mandala with red hearts around it"/>
    <circle class="mandala mandala--corner-top" cx="1045" cy="85" r="195"
            fill="url(#mandala-corner-tones)"
            role="img" aria-label="Corner mandala in blue, yellow and pink with a spiked outer ring"/>
    <circle class="mandala mandala--flower-bottom" cx="968" cy="835" r="210"
            fill="url(#mandala-flower-tones)"
            role="img" aria-label="Flower-shaped mandala with colourful petals rising from the bottom edge"/>
  </svg>

  <h1 class="headline">Experience the Magic of<br>Mandala Making</h1>
  <p class="class-date">Next Class will be held :</p>
</main>
</body>
</html>
```